Business Management Fortress

Assist with enhancing a powerpoint slide by providing a few design options for consideration. I have a template but open to any creative ideas.

Internal employees and stakeholders

Business Management, Finance, Accounting

• Maintain a fortress, temple, or pyramid schema
• Scenic Background

```html
<!DOCTYPE html>
<html lang="en">
<head>
<meta charset="utf-8">
<title>Business Management Fortress</title>
<link href="https://fonts.googleapis.com/css2?family=Montserrat:wght@500;700&display=swap" rel="stylesheet">
<style>
  :root {
    --ink: #111111;
    --sky-top: #e6eaeb;
    --sky-mid: #eef0ef;
    --sand: #efebe6;
    --gold: #f6c400;
    --gold-dark: #e59a00;
    --red: #fd2638;
    --red-dark: #b51b27;
    --crimson: #bb124b;
    --crimson-dark: #7e0a31;
    --cyan: #00cbe8;
    --cyan-dark: #0aa3ba;
    --navy: #0a5585;
    --navy-dark: #063a5a;
    --band: #ffffff;
  }
  * { margin: 0; padding: 0; box-sizing: border-box; }
  html, body { width: 1200px; height: 675px; overflow: hidden; }
  body { font-family: "Montserrat", Arial, sans-serif; color: var(--ink); }
  .slide { position: relative; width: 1200px; height: 675px; overflow: hidden; }
  .scenery {
    position: absolute; inset: 0;
    background:
      radial-gradient(ellipse 420px 260px at 600px 400px, rgba(207,201,192,.55), transparent 70%),
      linear-gradient(180deg, var(--sky-top) 0%, var(--sky-mid) 55%, var(--sand) 78%, #f4f1ed 100%);
  }
  .pyramid { position: absolute; left: 0; top: 0; }
  .tier-title {
    position: absolute; font-weight: 700; font-size: 20px; line-height: 1; white-space: nowrap;
  }
  .tier-copy {
    position: absolute; font-weight: 500; font-size: 9.6px; line-height: 17px; width: 200px; white-space: nowrap;
  }
  .pillar-title {
    position: absolute; font-weight: 700; font-size: 20px; line-height: 26px; white-space: nowrap;
  }
  .fiduciary {
    position: absolute; left: 384px; width: 430px; top: 413px; text-align: center;
    font-weight: 700; font-size: 20.5px; line-height: 26px; white-space: nowrap;
  }
  .foundation {
    position: absolute; left: 340px; width: 520px; top: 496px; text-align: center;
    color: #fff; font-weight: 500; font-size: 14.5px; line-height: 27px; white-space: nowrap;
  }
  .slide-code { position: absolute; right: 14px; bottom: 18px; font-size: 11px; font-weight: 500; }
</style>
</head>
<body>
<main class="slide">
  <div class="scenery" role="img" aria-label="Soft photograph of ancient stone pyramids in a desert under a pale sky"></div>

  <svg class="pyramid" width="1200" height="675" viewBox="0 0 1200 675" aria-hidden="true">
    <polygon class="pillar-band" points="601,88 691,86 901,463 814,463" fill="var(--band)"/>

    <polygon points="551,176 564,195 575,176" fill="var(--gold-dark)"/>
    <polygon points="626,176 638,195 650,176" fill="var(--gold-dark)"/>
    <polygon points="601,89 650,176 551,176" fill="var(--gold)"/>

    <polygon points="496,271 508,291 520,271" fill="var(--red-dark)"/>
    <polygon points="681,271 693,291 705,271" fill="var(--red-dark)"/>
    <polygon points="539,195 661,195 705,271 496,271" fill="var(--red)"/>

    <polygon points="440,367 452,386 464,367" fill="var(--crimson-dark)"/>
    <polygon points="736,367 748,386 760,367" fill="var(--crimson-dark)"/>
    <polygon points="483,293 717,293 760,367 440,367" fill="var(--crimson)"/>

    <polygon points="384,463 396,483 408,463" fill="var(--cyan-dark)"/>
    <polygon points="790,463 802,483 814,463" fill="var(--cyan-dark)"/>
    <polygon points="427,389 772,389 814,463 384,463" fill="var(--cyan)"/>

    <polygon points="322,569 334,588 346,569" fill="var(--navy-dark)"/>
    <polygon points="853,569 865,588 877,569" fill="var(--navy-dark)"/>
    <polygon points="371,484 829,484 877,569 322,569" fill="var(--navy)"/>

    <g fill="none" stroke-width="1.6">
      <circle cx="601" cy="141" r="15" stroke="#1a1a1a" role="img" aria-label="Leadership team icon"/>
      <circle cx="601" cy="233" r="17" stroke="#ffffff" role="img" aria-label="Hands joining puzzle pieces icon"/>
      <circle cx="601" cy="330" r="18" stroke="#ffffff" role="img" aria-label="Financial growth icon"/>
      <circle cx="680" cy="142" r="17" stroke="var(--gold-dark)" role="img" aria-label="Connected people icon"/>
      <circle cx="724" cy="223" r="18" stroke="var(--red)" role="img" aria-label="Idea bulb with gear icon"/>
      <circle cx="776" cy="316" r="18" stroke="var(--crimson)" role="img" aria-label="Digital brain icon"/>
      <circle cx="827" cy="411" r="18" stroke="var(--cyan)" role="img" aria-label="Handshake with gear icon"/>
    </g>
  </svg>

  <h2 class="tier-title" style="left:319px; top:105px;">LEADER</h2>
  <p class="tier-copy" style="left:321px; top:129px;">Lorem ipsum dolor sit amet, consec-<br>tetur adipiscing elit, sed do eiusmod<br>tempor incididunt ut labore</p>

  <h2 class="tier-title" style="left:247px; top:208px;">PARTNER</h2>
  <p class="tier-copy" style="left:249px; top:232px;">Lorem ipsum dolor sit amet, consec-<br>tetur adipiscing elit, sed do eiusmod<br>tempor incididunt ut labore</p>

  <h2 class="tier-title" style="left:177px; top:310px;">PROFITABILITY</h2>
  <p class="tier-copy" style="left:179px; top:335px;">Lorem ipsum dolor sit amet, consec-<br>tetur adipiscing elit, sed do eiusmod<br>tempor incididunt ut labore</p>

  <h3 class="pillar-title" style="left:775px; top:124px;">PEOPLE</h3>
  <h3 class="pillar-title" style="left:792px; top:202px;">INNOVATION</h3>
  <h3 class="pillar-title" style="left:864px; top:285px;">BUSINESS<br>INTELLIGENCE</h3>
  <h3 class="pillar-title" style="left:899px; top:385px;">STRATEGIC<br>ALLIANCES</h3>

  <p class="fiduciary">FIDUCIARY RESPONSIBILITIES</p>
  <p class="foundation">Accurate Financials / Internal Controls / Brand Protection /<br>Compliance / Ethics / Cost Management</p>

  <span class="slide-code">C48</span>
</main>
</body>
</html>
```